Business Card Design for sports performance / psychology company

You can see my website that this is based upon here:
http://www.trelvanedge.co.uk

More than happy to answer any additional questions that you might have

** Happy for any images from Pixelvault to be used. If I go with your design I will purchase the image for you to use

Target Market(s)

Football players

Industry/Entity Type

Business

Contact Information for Business Card

Name: Clive Arnott
Title: Clinical Hypnotherapist & Strategist
Email address: clive@trelvanedge.co.uk
Tel: 07912486015

Font styles to use
Other font styles liked:
• Same font as on website. I'm not actually sure what it is

Requirements
Must have
• Tagline:
• Talent x Focus = Results
• Don't put form down to chance
Nice to have
• Happy for designers to be creative
Should not have

```html
<!DOCTYPE html>
<html lang="en">
<head>
<meta charset="utf-8">
<title>Trelvan Edge – Business Card</title>
<link rel="stylesheet" href="https://fonts.googleapis.com/css2?family=Jost:wght@400&family=Lato:wght@400;700&display=swap">
<style>
  :root {
    --navy: #221c48;
    --paper: #ffffff;
    --stage: #222222;
    --ink: #2a2a2a;
  }
  * { margin: 0; padding: 0; box-sizing: border-box; }
  html, body {
    width: 1189px; height: 1200px; overflow: hidden;
    background: var(--stage);
    font-family: "Lato", sans-serif;
  }
  .card {
    position: absolute; left: 171px; width: 856px; height: 488px; overflow: hidden;
  }
  .card--front { top: 67px; background: var(--navy); color: var(--paper); text-align: center; }
  .card--back { top: 626px; background: var(--paper); color: var(--navy); }

  .front__mark {
    position: absolute; left: 388px; top: 134px; width: 80px; height: 80px;
    border: 3px solid var(--paper); border-radius: 50%;
  }
  .front__brand {
    position: absolute; left: 0; right: 0; top: 232px;
    font-family: "Jost", sans-serif; font-weight: 400; font-size: 70px; line-height: 1;
    letter-spacing: 1px;
  }
  .front__tagline {
    position: absolute; left: 0; right: 0; top: 324px;
    font-size: 28px; line-height: 1;
  }

  .back__band { position: absolute; left: 0; top: 0; width: 105px; height: 100%; background: var(--navy); }
  .back__rule { position: absolute; left: 109px; top: 0; width: 6px; height: 100%; background: var(--navy); }
  .back__mark {
    position: absolute; left: 42px; top: 66px; width: 114px; height: 114px;
    border-radius: 50%; background: var(--paper); border: 8px solid var(--navy);
    box-shadow: 0 0 0 8px var(--paper);
  }
  .back__brand {
    position: absolute; left: 188px; top: 90px;
    font-family: "Jost", sans-serif; font-weight: 400; font-size: 58px; line-height: 1;
    letter-spacing: 1px;
  }
  .person { position: absolute; left: 199px; top: 280px; }
  .person__name { font-size: 33px; font-weight: 400; line-height: 1; }
  .person__name strong { font-weight: 700; }
  .person__title { font-size: 22px; color: var(--ink); margin-top: 6px; }

  .contacts { position: absolute; left: 200px; top: 370px; list-style: none; }
  .contacts li { display: flex; align-items: center; height: 27px; font-size: 22px; color: var(--ink); }
  .contacts li.phone { font-size: 25px; }
  .contacts svg { width: 24px; height: 24px; margin-right: 11px; flex: none; }

  .social { position: absolute; left: 664px; top: 414px; display: flex; gap: 20px; }
  .social span { width: 34px; height: 34px; background: var(--navy); display: block; }
</style>
</head>
<body>
  <section class="card card--front">
    <div class="front__mark"></div>
    <h1 class="front__brand">TRELVAN EDGE</h1>
    <p class="front__tagline">Talent x Focus = Results</p>
  </section>

  <section class="card card--back">
    <div class="back__band"></div>
    <div class="back__rule"></div>
    <div class="back__mark"></div>
    <h2 class="back__brand">TRELVAN EDGE</h2>

    <div class="person">
      <p class="person__name"><strong>Clive</strong> Arnott</p>
      <p class="person__title">Clinical Hypnotherapist &amp; Strategist</p>
    </div>

    <ul class="contacts">
      <li class="phone">
        <svg viewBox="0 0 24 24" aria-hidden="true"><rect width="24" height="24" fill="#221c48"/><path d="M5 9c0-3 14-3 14 0v2h-4v-2H9v2H5z M7 12h10l2 6H5z" fill="#fff"/></svg>
        07912486015
      </li>
      <li>
        <svg viewBox="0 0 24 24" aria-hidden="true"><rect width="24" height="24" fill="#221c48"/><rect x="4" y="6.5" width="16" height="11" fill="none" stroke="#fff" stroke-width="1.5"/><path d="M4 6.5l8 6 8-6M4 17.5l6-5M20 17.5l-6-5" fill="none" stroke="#fff" stroke-width="1.3"/></svg>
        clive@trelvanedge.co.uk
      </li>
      <li>
        <svg viewBox="0 0 24 24" aria-hidden="true"><rect width="24" height="24" fill="#221c48"/><g fill="none" stroke="#fff" stroke-width="1.3"><circle cx="12" cy="12" r="7"/><ellipse cx="12" cy="12" rx="3" ry="7"/><path d="M5 12h14M6 8.5h12M6 15.5h12"/></g></svg>
        www.trelvanedge.co.uk
      </li>
    </ul>

    <div class="social" aria-label="Social media links">
      <span></span><span></span><span></span>
    </div>
  </section>
</body>
</html>
```